Make a logo repeat back ground for a banner
Step and Repeat Backdrop Media Logo banner
Not quite sure what it is called
But want a banner designed with our logo repeated
Thanks

76 cm x 244 cm
http://www.quorvelo.com.au/banners.aspx?txi=58302&xnid=TopNav_Banners+(linked+item)_Signs+%26+Banners_All+Products&xnav=TopNav

Media

```html
<!DOCTYPE html>
<html lang="en">
<head>
<meta charset="utf-8">
<title>Korvan Diesel – Step and Repeat Banners</title>
<link href="https://fonts.googleapis.com/css2?family=Russo+One&display=swap" rel="stylesheet">
<style>
  :root {
    --page-bg: #efe9e2;
    --green-banner: #52f520;
    --green-mark: #86d83c;
    --red-banner: #c9264a;
    --red-banner-light: #ef5566;
    --red-banner-dark: #b91f45;
    --red-mark: #f07a52;
    --red-mark-large: #f2875a;
  }
  * { margin: 0; padding: 0; box-sizing: border-box; }
  html, body {
    width: 1200px;
    height: 1000px;
    overflow: hidden;
    background: var(--page-bg);
    font-family: "Russo One", sans-serif;
  }
  .canvas {
    position: relative;
    width: 1200px;
    height: 1000px;
  }
  .banner {
    position: absolute;
    left: 24px;
    width: 1145px;
    height: 316px;
    overflow: hidden;
  }
  .banner--green {
    top: 52px;
    background: var(--green-banner);
  }
  .banner--red {
    top: 520px;
    background: radial-gradient(ellipse at 50% 42%, var(--red-banner-light) 0%, var(--red-banner) 55%, var(--red-banner-dark) 100%);
  }
  .repeat-mark {
    position: absolute;
    width: 92px;
    display: flex;
    align-items: center;
    gap: 5px;
    font-size: 15px;
    line-height: 1.05;
    letter-spacing: 0.5px;
    text-transform: uppercase;
  }
  .repeat-mark::before {
    content: "";
    flex: 0 0 10px;
    height: 10px;
    background: currentColor;
  }
  .banner--green .repeat-mark { color: var(--green-mark); }
  .banner--red .repeat-mark { color: var(--red-mark); }
  .hero-mark {
    position: absolute;
    left: 446px;
    top: 52px;
    width: 320px;
    display: flex;
    flex-direction: column;
    align-items: center;
    color: var(--red-mark-large);
    font-size: 58px;
    line-height: 1.05;
    letter-spacing: 2px;
    text-transform: uppercase;
    text-align: center;
  }
  .hero-mark::after {
    content: "";
    width: 56px;
    height: 56px;
    margin-top: 22px;
    background: currentColor;
  }
</style>
</head>
<body>
<main class="canvas">

  <section class="banner banner--green" aria-label="Green step and repeat banner">
    <div class="repeat-mark" style="left:28px;top:36px">Korvan<br>Diesel</div>
    <div class="repeat-mark" style="left:294px;top:22px">Korvan<br>Diesel</div>
    <div class="repeat-mark" style="left:511px;top:36px">Korvan<br>Diesel</div>
    <div class="repeat-mark" style="left:768px;top:36px">Korvan<br>Diesel</div>
    <div class="repeat-mark" style="left:1026px;top:8px">Korvan<br>Diesel</div>
    <div class="repeat-mark" style="left:176px;top:104px">Korvan<br>Diesel</div>
    <div class="repeat-mark" style="left:364px;top:88px">Korvan<br>Diesel</div>
    <div class="repeat-mark" style="left:559px;top:118px">Korvan<br>Diesel</div>
    <div class="repeat-mark" style="left:901px;top:120px">Korvan<br>Diesel</div>
    <div class="repeat-mark" style="left:176px;top:202px">Korvan<br>Diesel</div>
    <div class="repeat-mark" style="left:689px;top:186px">Korvan<br>Diesel</div>
    <div class="repeat-mark" style="left:364px;top:216px">Korvan<br>Diesel</div>
    <div class="repeat-mark" style="left:28px;top:244px">Korvan<br>Diesel</div>
    <div class="repeat-mark" style="left:534px;top:244px">Korvan<br>Diesel</div>
    <div class="repeat-mark" style="left:831px;top:244px">Korvan<br>Diesel</div>
    <div class="repeat-mark" style="left:1026px;top:220px">Korvan<br>Diesel</div>
  </section>

  <section class="banner banner--red" aria-label="Red step and repeat banner">
    <div class="repeat-mark" style="left:28px;top:36px">Korvan<br>Diesel</div>
    <div class="repeat-mark" style="left:246px;top:16px">Korvan<br>Diesel</div>
    <div class="repeat-mark" style="left:768px;top:36px">Korvan<br>Diesel</div>
    <div class="repeat-mark" style="left:1026px;top:6px">Korvan<br>Diesel</div>
    <div class="repeat-mark" style="left:176px;top:104px">Korvan<br>Diesel</div>
    <div class="repeat-mark" style="left:364px;top:88px">Korvan<br>Diesel</div>
    <div class="repeat-mark" style="left:901px;top:120px">Korvan<br>Diesel</div>
    <div class="repeat-mark" style="left:28px;top:148px">Korvan<br>Diesel</div>
    <div class="repeat-mark" style="left:768px;top:150px">Korvan<br>Diesel</div>
    <div class="repeat-mark" style="left:1051px;top:150px">Korvan<br>Diesel</div>
    <div class="repeat-mark" style="left:176px;top:202px">Korvan<br>Diesel</div>
    <div class="repeat-mark" style="left:341px;top:210px">Korvan<br>Diesel</div>
    <div class="repeat-mark" style="left:28px;top:232px">Korvan<br>Diesel</div>
    <div class="repeat-mark" style="left:831px;top:234px">Korvan<br>Diesel</div>
    <div class="repeat-mark" style="left:979px;top:234px">Korvan<br>Diesel</div>
    <div class="hero-mark">Korvan<br>Diesel</div>
  </section>

</main>
</body>
</html>
```